Talvique Hotels Business Card and Logo

We need a business card design for a hotel group. I saw a hotel card you designed and really liked it. We have multiple properties with different brands. Were hoping that the card would be unique and find a way to list out all our properties. Our web address is www.talviquehotels.com. I have attached some photos of card designs I like.

Industry/Entity Type

Hotel

Contact Information for Business Card

Scott CurranReneson HotelsChief Operating Officer56 Madera DriveCorte Madera, CA 94925Office 415-891-5013Cell 707-5550143

```html
<!DOCTYPE html>
<html lang="en">
<head>
<meta charset="UTF-8">
<title>Talvique Hotels Business Card</title>
<link href="https://fonts.googleapis.com/css2?family=Montserrat:wght@400;500;700&display=swap" rel="stylesheet">
<style>
  :root {
    --stage: #e9e8ec;
    --paper: #f7f7f6;
    --ink: #47455f;
    --ink-soft: #2f2e3a;
    --navy-top: #4a4865;
    --navy-bottom: #6d6b82;
    --on-navy: #f4f3f6;
  }
  * { margin: 0; padding: 0; box-sizing: border-box; }
  html, body {
    width: 1200px;
    height: 985px;
    overflow: hidden;
    background: var(--stage);
    font-family: "Montserrat", sans-serif;
  }
  .stage {
    position: relative;
    width: 1200px;
    height: 985px;
    display: flex;
    justify-content: center;
    align-items: center;
    gap: 80px;
  }
  .card {
    width: 400px;
    height: 700px;
    border-radius: 4px;
    box-shadow: 0 10px 30px rgba(40, 38, 55, 0.18);
    display: flex;
    flex-direction: column;
    align-items: center;
    text-align: center;
  }
  .card--front {
    background: var(--paper);
    color: var(--ink-soft);
    padding-top: 110px;
  }
  .card--back {
    background: linear-gradient(160deg, var(--navy-top) 0%, var(--navy-top) 45%, var(--navy-bottom) 100%);
    color: var(--on-navy);
    justify-content: center;
  }
  .brand {
    display: flex;
    flex-direction: column;
    align-items: center;
    gap: 22px;
  }
  .brand__dot {
    width: 58px;
    height: 58px;
    border-radius: 50%;
    border: 3px solid currentColor;
  }
  .brand__name {
    font-weight: 500;
    font-size: 38px;
    letter-spacing: 0.5px;
    line-height: 1.1;
  }
  .card--front .brand { color: var(--ink); }
  .card--back .brand { color: var(--on-navy); }
  .person { margin-top: 130px; }
  .person__name {
    font-weight: 700;
    font-size: 24px;
    letter-spacing: 1px;
    color: var(--ink);
    text-transform: uppercase;
  }
  .person__title {
    margin-top: 8px;
    font-size: 17px;
    color: var(--ink-soft);
  }
  .contact-icons {
    margin-top: 40px;
    display: flex;
    gap: 18px;
  }
  .contact-icons svg { width: 36px; height: 36px; }
  .phones, .address {
    font-size: 17px;
    line-height: 1.5;
    color: var(--ink-soft);
  }
  .phones { margin-top: 18px; }
  .address { margin-top: 26px; }
</style>
</head>
<body>
<main class="stage">
  <section class="card card--front">
    <div class="brand">
      <span class="brand__dot"></span>
      <span class="brand__name">Talvique Hotels</span>
    </div>
    <div class="person">
      <p class="person__name">Brent Holloway</p>
      <p class="person__title">Chief Operating Officer</p>
    </div>
    <div class="contact-icons">
      <svg viewBox="0 0 36 36" aria-label="Office phone">
        <circle cx="18" cy="18" r="16" fill="none" stroke="#47455f" stroke-width="1.8"/>
        <path d="M12 11c1-1 2-1 3 0l1.5 2.5c.5 1 0 1.8-.7 2.3-.6.4-.6 1 0 2l2 2.3c.8.8 1.4.9 2 .3.6-.7 1.4-1.1 2.3-.6l2.4 1.5c1 .8.9 1.8 0 2.7-1.6 1.6-4.2 1.7-7.5-1.3-3.6-3.2-6.3-7.6-5-11.7z" fill="#47455f"/>
        <path d="M20 10.5a6 6 0 0 1 5.5 5.5M20 13.5a3 3 0 0 1 2.5 2.5" fill="none" stroke="#47455f" stroke-width="1.4" stroke-linecap="round"/>
      </svg>
      <svg viewBox="0 0 36 36" aria-label="Mobile phone">
        <circle cx="18" cy="18" r="16" fill="none" stroke="#47455f" stroke-width="1.8"/>
        <rect x="13" y="9" width="10" height="18" rx="2" fill="none" stroke="#47455f" stroke-width="1.6"/>
        <line x1="16.5" y1="24" x2="19.5" y2="24" stroke="#47455f" stroke-width="1.4" stroke-linecap="round"/>
      </svg>
    </div>
    <div class="phones">
      <p>415-555-0186</p>
      <p>707-5550143</p>
    </div>
    <div class="address">
      <p>83 Pellwick Lane</p>
      <p>Fenwick Bay, CA 94990</p>
    </div>
  </section>

  <section class="card card--back">
    <div class="brand">
      <span class="brand__dot"></span>
      <span class="brand__name">Talvique Hotels</span>
    </div>
  </section>
</main>
</body>
</html>
```